Debt Collection Website Design! We are the solution for landlords to get paid what they are owed.

We are a 3rd party debt collection company that specializes in Residential and Commercial real estate debt collection. We help landlords recover money from past residents by being fair, friendly and aggressive. We also collect/buy/sell/trade civil judgments won resulting from anything from automobile accidents to evictions to a pet zebra getting stolen. We buy single judgments to large portfolios, we also collect judgments for a nominal fee.

I would like a new, modern, easy to navigate website. A spot that we can post news stories or updated information about our company. I have included our company logo that must be on the top of the page. Feel free to ask any questions that will help get the process going.

Target Market(s)

Landlords, small to large apartment complex. Real estate services and lawyers.

Industry/Entity Type

Real Estate

Number of Pages Required

3 page

Requirements
Must have
• Company logo which has been attached. A page where we can explain the collection process, fees and placement. A page where we can explain judgments, collection vs. selling, placement form. I am open to any font/designs and willing to work with anyone.
Nice to have
• Nice to have a spot on the homepage to place news articles about ourselves and our industry.
Should not have
• I don't want it over crowded. Simple, sleek and easy to navigate is best. No gavels on any of the pages. It cannot look legal, say/show anything that we use legal powers to collect. We are not a law office, we don't practice law, we are 3rd party debt collection agency.

```html
<!DOCTYPE html>
<html lang="en">
<head>
<meta charset="utf-8">
<title>Halvorsen Recovery, LLC</title>
<link href="https://fonts.googleapis.com/css2?family=Cinzel:wght@400;700&family=Open+Sans:wght@400;600&display=swap" rel="stylesheet">
<style>
:root{
  --navy:#1c2f6e;
  --navy-dark:#14245a;
  --text:#7a7a7a;
  --heading:#1e1e1e;
  --rule:#e2e2e2;
  --footer:#1c1c1c;
  --footer-base:#121212;
  --footer-text:#a9a9a9;
  --date:#8c96a3;
}
*{margin:0;padding:0;box-sizing:border-box}
html,body{width:847px;height:1200px;overflow:hidden;background:#fff}
body{position:relative;font-family:"Open Sans",sans-serif;color:var(--text)}
.abs{position:absolute}
.serif{font-family:"Cinzel",serif}

.header{left:0;top:0;width:847px;height:62px;background:#fff;box-shadow:0 1px 3px rgba(0,0,0,.12);z-index:2}
.brand{left:70px;top:13px;display:flex;align-items:center;gap:8px}
.brand-mark{width:30px;height:30px;background:var(--navy)}
.brand-name{font-family:"Cinzel",serif;color:var(--navy);font-size:17px;line-height:16px;font-weight:400}
.brand-name small{display:block;font-size:11px;letter-spacing:.5px}
.nav{right:69px;top:27px;display:flex;gap:25px;font-family:"Cinzel",serif;font-size:9.5px;color:#666;letter-spacing:.3px}
.nav .active{color:var(--navy);font-weight:700}

.hero{left:0;top:62px;width:847px;height:356px;background:linear-gradient(100deg,#3c4a3a 0%,#6f7c8f 30%,#c9d0da 48%,#8e97a4 70%,#3a3f3a 100%)}
.hero-shadow{left:20px;top:418px;width:807px;height:14px;background:radial-gradient(ellipse at top,rgba(0,0,0,.18),rgba(0,0,0,0) 70%)}
.arrow{top:206px;height:52px;width:38px}
.arrow.next{right:0;background:rgba(40,40,40,.55)}
.arrow.prev{left:0}

.photo{background:linear-gradient(135deg,#8a93a3,#c6ccd6);box-shadow:3px 3px 6px rgba(0,0,0,.2)}
.service{width:225px}
.service h3{font-family:"Cinzel",serif;font-size:12.5px;color:var(--heading);font-weight:400;letter-spacing:.4px;margin-top:13px}
.service .bar,.section-title .bar{width:30px;height:2px;background:var(--navy);margin-top:9px}
.service p{font-size:8.3px;line-height:15.2px;margin-top:12px}
.btn{display:inline-block;background:var(--navy);color:#fff;font-family:"Cinzel",serif;font-size:9.5px;padding:0 15px;height:25px;line-height:25px;border-radius:2px;border-bottom:2px solid var(--navy-dark)}

.divider{left:0;top:724px;width:847px;height:1px;background:var(--rule)}
.section-title h2{font-family:"Cinzel",serif;font-size:12.5px;color:var(--heading);font-weight:400;letter-spacing:.5px}
.frame{background:#e4e4e4;padding:5px;border-radius:2px}
.frame div{width:100%;height:100%}
.welcome-text{left:70px;top:922px;width:440px;font-size:8.3px;line-height:14.5px;color:#666}

.news-item{left:568px;width:210px;height:70px;display:flex;gap:11px;border-bottom:1px solid var(--rule)}
.date{width:47px;height:54px;background:var(--date);color:#fff;text-align:center;border-radius:2px;padding-top:9px;flex:none}
.date span{display:block;font-size:11px;line-height:13px}
.date b{display:block;font-size:14px;font-weight:600;line-height:20px}
.news-item h4{font-size:9.5px;color:var(--navy);font-weight:400;margin-top:3px}
.news-item p{font-size:8px;line-height:13px;color:#666;margin-top:4px}

.footer{left:0;top:1059px;width:847px;height:98px;background:var(--footer)}
.footer-base{left:0;top:1157px;width:847px;height:43px;background:var(--footer-base);font-size:7.5px;color:#9a9a9a;text-align:center;line-height:43px}
.footer h5{font-family:"Cinzel",serif;font-size:10px;color:#bdbdbd;font-weight:400;letter-spacing:.6px}
.footer p{font-size:8.3px;line-height:16px;color:var(--footer-text);margin-top:12px}
.footer-brand{left:70px;top:32px;display:flex;align-items:center;gap:8px}
.footer-brand .brand-mark{background:#555}
.footer-brand .brand-name{color:#555}
.social{display:flex;gap:8px;margin-top:12px}
.social i{width:23px;height:23px;border-radius:50%;display:block}
</style>
</head>
<body>

<header class="abs header">
  <div class="abs brand"><span class="brand-mark"></span><span class="brand-name">Halvorsen<small>Recovery, LLC</small></span></div>
  <nav class="abs nav"><span class="active">HOME</span><span>ABOUT US</span><span>SERVICES</span><span>PROJECTS</span><span>NEWS</span><span>SUPPORT</span><span>CONTACT US</span></nav>
</header>

<div class="abs hero" role="img" aria-label="City financial district with tall glass office towers and a large currency sculpture"></div>
<div class="abs hero-shadow"></div>
<svg class="abs arrow prev" viewBox="0 0 38 52"><path d="M22 14 L12 26 L22 38" fill="none" stroke="#fff" stroke-width="2"/></svg>
<svg class="abs arrow next" viewBox="0 0 38 52"><path d="M16 14 L26 26 L16 38" fill="none" stroke="#fff" stroke-width="2"/></svg>

<section class="abs service" style="left:70px;top:443px">
  <div class="photo" style="height:110px;width:217px;background:linear-gradient(135deg,#a9a7a6,#e2dfdc)" role="img" aria-label="Team of business people reviewing a tablet together"></div>
  <h3>Residential Debt Collection</h3><div class="bar"></div>
  <p>We are a debt collection company that specializes in Residential and Commercial real estate debt collection. We help landlords recover money from past residents by being fair, friendly and aggressive.</p>
  <div style="margin-top:11px"><span class="btn">MORE</span></div>
</section>
<section class="abs service" style="left:316px;top:443px">
  <div class="photo" style="height:110px;width:217px;background:linear-gradient(90deg,#9fb4c8,#5d86b7 55%,#2a4f9a)" role="img" aria-label="Modern commercial office buildings against a blue sky"></div>
  <h3>Commercial Real Estate</h3><div class="bar"></div>
  <p>Sed ut perspiciatis unde omnis iste natus errolore or sit voluptatem accusantium doloremlore ipque laudantium, totam rem aperiam, eaque ipsa quae ab illo inventore veritatis et quasi architloremecto beatae vitae.</p>
  <div style="margin-top:11px"><span class="btn">MORE</span></div>
</section>
<section class="abs service" style="left:558px;top:443px">
  <div class="photo" style="height:110px;width:217px;background:linear-gradient(135deg,#5b4f4a,#c99a86 55%,#6d6461)" role="img" aria-label="Hands sheltering a small toy car"></div>
  <h3>Automobile Accidents</h3><div class="bar"></div>
  <p>We also collect/buy/sell/trade civil judgments won resu lting from anything from automobile accidents eaq ue ipsa quae ab illo inventore veritatis et quloreasi architlo remecto beatae vitae.</p>
  <div style="margin-top:11px"><span class="btn">MORE</span></div>
</section>

<div class="abs divider"></div>

<div class="abs section-title" style="left:71px;top:748px"><h2>Welcome to Halvorsen!!</h2><div class="bar"></div></div>
<div class="abs frame" style="left:70px;top:797px;width:208px;height:111px"><div style="background:linear-gradient(135deg,#6f87a8,#d8dde3 60%,#9aa2ad)" role="img" aria-label="Colleagues meeting around a laptop in an office"></div></div>
<div class="abs frame" style="left:301px;top:797px;width:207px;height:111px"><div style="background:linear-gradient(135deg,#3b3f4a,#e7ebf0 55%,#3a6fc2)" role="img" aria-label="Hands reviewing financial charts on paper and a tablet"></div></div>
<p class="abs welcome-text">Sed ut perspiciatis unde omnis iste natus error sit voluptatem accusantium doloremque laudantium, totam rem aperiam, eaque ipsa quae ab illo inventore veritatis et quasi architecto beatae vitae dicta sunt explicabo. Nemo enim ipsam voluptatem quia voluptas sit aspernatur aut odit aut fugit, sed quia consequuntur magni dolores eos qui ratione voluptatem sequi nesciunt.</p>
<div class="abs" style="left:70px;top:992px"><span class="btn" style="padding:0 18px;height:27px;line-height:27px">MORE</span></div>

<div class="abs section-title" style="left:569px;top:748px"><h2>Latest News</h2><div class="bar"></div></div>
<article class="abs news-item" style="top:797px"><div class="date"><span>FEB</span><b>2015</b></div><div><h4>Sed ut perspiciatis unde omn</h4><p>Aus error sit voluptatem accusantium. doloremque laudantium, totam rem</p></div></article>
<article class="abs news-item" style="top:881px"><div class="date"><span>FEB</span><b>2015</b></div><div><h4>Sed ut perspiciatis unde omn</h4><p>Aus error sit voluptatem accusantium. doloremque laudantium, totam rem</p></div></article>
<article class="abs news-item" style="top:964px;border-bottom:none"><div class="date"><span>FEB</span><b>2015</b></div><div><h4>Sed ut perspiciatis unde omn</h4><p>Aus error sit voluptatem accusantium. doloremque laudantium, totam rem</p></div></article>

<footer class="abs footer">
  <div class="abs footer-brand"><span class="brand-mark"></span><span class="brand-name">Halvorsen<small>Recovery, LLC</small></span></div>
  <div class="abs" style="left:261px;top:25px"><h5>Let's Talk</h5><p>Phone: 555.210.4400<br>Fax: 555.210.4401</p></div>
  <div class="abs" style="left:416px;top:25px"><h5>Find Us</h5><p>Debt recovery company<br>4820 Linden Avenue Fairview, MO 64000</p></div>
  <div class="abs" style="left:632px;top:25px"><h5>Follow Us</h5>
    <div class="social"><i style="background:#3aa8e6"></i><i style="background:#f08a24"></i><i style="background:#3b5a9a"></i><i style="background:#d8333f"></i><i style="background:#555"></i></div>
  </div>
</footer>
<div class="abs footer-base">© 2015 Debt recovery company. all rights are reserved</div>

</body>
</html>
```